The Copper Kite Website Redesign

I want a new design and website for www.thecopperkitebrookvale.com where part of the home page includes our daily specials from our POS Toast to be pulled from API. I have included photos and links to give you a better feel for the style of our restaurant.

Coding

Coded - Design and coding required

```html
<!DOCTYPE html>
<html lang="en">
<head>
<meta charset="utf-8">
<title>The Copper Kite – A Finer Diner</title>
<link href="https://fonts.googleapis.com/css2?family=Londrina+Solid:wght@400;900&family=Montserrat:wght@400;500;600;700&display=swap" rel="stylesheet">
<style>
:root{
  --orange:#f7941d;
  --orange-deep:#f08a0c;
  --cream:#fffbd3;
  --ink:#111111;
  --text:#333333;
  --muted:#666666;
  --line:#e6e6e6;
  --faq:#f1f1f1;
  --white:#ffffff;
}
*{margin:0;padding:0;box-sizing:border-box}
html,body{width:1200px;height:4274px;overflow:hidden}
body{position:relative;font-family:"Montserrat",sans-serif;color:var(--text);background:var(--white)}
.abs{position:absolute}
.display{font-family:"Londrina Solid",sans-serif;font-weight:400;color:var(--ink);text-transform:uppercase;letter-spacing:-0.5px;white-space:nowrap}
.btn{position:absolute;display:flex;align-items:center;justify-content:center;background:var(--orange);color:var(--white);font-weight:700;font-size:15px;text-transform:uppercase;letter-spacing:.3px}

/* top bar */
.topbar{left:0;top:0;width:1200px;height:32px;background:var(--orange);color:var(--white);font-size:13px;font-weight:500}
.topbar .item{position:absolute;top:0;height:32px;display:flex;align-items:center;gap:8px;white-space:nowrap}
.topbar .item b{font-weight:700}
.topbar .sep{position:absolute;top:0;width:1px;height:32px;background:rgba(255,255,255,.6)}

/* header */
.header{left:0;top:32px;width:1200px;height:88px;background:var(--cream)}
.brand{position:absolute;left:110px;top:20px;line-height:1;white-space:nowrap}
.brand .name{font-family:"Montserrat",sans-serif;font-weight:700;font-size:24px;color:var(--ink);letter-spacing:-.5px}
.brand .tag{font-size:13px;font-weight:700;color:var(--ink);margin-top:6px}
.nav{position:absolute;top:34px;left:368px;font-size:15px;color:var(--text)}
.nav a{position:absolute;white-space:nowrap;text-decoration:none;color:var(--text)}
.nav a.active{color:var(--orange)}
.nav a.active::after{content:"";position:absolute;left:0;right:0;top:40px;height:3px;background:var(--orange)}
.cart-count{position:absolute;left:1072px;top:20px;width:18px;height:18px;border-radius:50%;background:var(--orange);color:#fff;font-size:11px;font-weight:700;display:flex;align-items:center;justify-content:center}

/* hero */
.hero{left:0;top:120px;width:1200px;height:580px}
.hero-bg{position:absolute;inset:0;background:linear-gradient(100deg,#b9c2d1 0%,#d3d8e1 40%,#cfd3db 100%)}
.hero-photo{position:absolute;left:540px;top:0;width:660px;height:520px;background:radial-gradient(ellipse at 55% 50%,#d99a3c 0%,#c98532 35%,rgba(201,133,50,0) 72%)}
.hero .welcome{left:110px;top:90px;font-size:34px;line-height:40px}
.hero h1{position:absolute;left:108px;top:130px;font-size:84px;line-height:92px;font-weight:900}
.hero p{position:absolute;left:110px;top:240px;width:480px;font-size:15.5px;line-height:29px;color:var(--text)}

/* about */
.about-frame{left:106px;top:777px;width:462px;height:392px;background:#d8d8d8;border-radius:8px 8px 8px 30px;transform:skew(-1deg)}
.about-photo{left:124px;top:793px;width:444px;height:376px;border-radius:0 0 30px 30px;background:linear-gradient(160deg,#9aa4a8 0%,#5f5a45 40%,#d9c23f 70%,#e7cf45 100%)}
.about-title{left:627px;top:792px;font-size:48px;line-height:56px}
.about-text{left:627px;top:862px;width:450px;font-size:15.5px;line-height:30px}

/* specials */
.specials{left:0;top:1248px;width:1200px;height:676px}
.specials-title{left:0;top:1352px;width:1200px;text-align:center;color:var(--white);font-size:48px;line-height:56px}
.side-card{top:1439px;height:321px;background:#fde9b2;border-radius:8px;opacity:.45}
.sc-photo{position:absolute;top:6px;height:309px;background:linear-gradient(135deg,#8a5a2b,#c98b3e,#4e3a23)}
.card{left:226px;top:1439px;width:743px;height:321px;background:var(--cream);border-radius:8px}
.card .photo{position:absolute;left:6px;top:6px;width:332px;height:309px;background:radial-gradient(ellipse at 50% 50%,#6b3b1e 0%,#a96b2f 40%,#c9a070 75%,#7c6450 100%)}
.card h3{position:absolute;left:367px;top:26px;font-size:20px;font-weight:600;color:var(--ink)}
.card p{position:absolute;left:370px;top:68px;width:330px;font-size:13.5px;line-height:26px}
.card .meta{position:absolute;left:373px;top:186px;display:flex;gap:34px;font-size:13px;align-items:center}
.card .meta span{display:flex;align-items:center;gap:10px}
.arrow{position:absolute;width:52px;height:52px;border:2px solid var(--ink);border-radius:50%;background:var(--white);display:flex;align-items:center;justify-content:center}

/* menu */
.menu-title{left:0;top:1978px;width:1200px;text-align:center;font-size:48px;line-height:56px}
.dish{position:absolute;width:478px;height:210px;border:1.5px solid var(--line);border-radius:6px;background:var(--white)}
.dish .thumb{position:absolute;left:4px;top:4px;width:193px;height:200px;border-radius:6px}
.dish h4{position:absolute;left:212px;top:22px;font-size:20px;font-weight:600;color:var(--ink)}
.dish p{position:absolute;left:212px;top:60px;width:250px;font-size:13.5px;line-height:30px;color:var(--muted)}
.dish .price{position:absolute;left:212px;top:160px;font-size:19px;font-weight:700;color:var(--orange)}

/* faq */
.faq-title{left:0;top:3118px;width:1200px;text-align:center;font-size:48px;line-height:56px}
.faq{position:absolute;width:478px;height:45px;background:var(--faq);border-radius:3px;display:flex;align-items:center;padding:0 22px;font-size:15px;color:var(--text);justify-content:space-between}
.faq.open{background:var(--orange);color:var(--white)}
.faq .sign{font-size:22px;font-weight:400}
.faq-answer{left:133px;top:3277px;width:430px;font-size:13px;line-height:28px;color:var(--text)}

/* newsletter */
.newsletter{left:0;top:3445px;width:1200px;height:360px}
.news-title{left:108px;top:3572px;font-size:46px;line-height:54px;color:var(--white)}
.news-text{left:108px;top:3694px;width:680px;font-size:14px;line-height:28px;color:var(--white)}
.subscribe{left:876px;top:3584px;width:206px;height:56px;background:var(--ink);border-radius:6px;color:var(--white);font-size:16px;font-weight:600;display:flex;align-items:center;justify-content:center;text-transform:uppercase}

/* footer */
.footer{left:0;top:3801px;width:1200px;height:473px;background:var(--ink);color:var(--white)}
.footer .brand{left:110px;top:100px}
.footer .brand .name,.footer .brand .tag{color:var(--white)}
.social{position:absolute;top:204px;width:34px;height:34px;border-radius:50%;background:#2a2a2a}
.social.active{background:var(--orange)}
.fcol{position:absolute;top:80px}
.fcol h5{font-size:22px;font-weight:600;margin-bottom:22px;white-space:nowrap}
.fcol ul{list-style:none;font-size:14px;line-height:30px}
.contact .label{font-weight:700;display:flex;align-items:center;gap:8px;margin-left:-20px}
.contact .val{display:block}
.footer .rule{position:absolute;left:108px;top:415px;width:976px;height:1px;background:#888}
.copy{position:absolute;left:0;top:434px;width:1200px;text-align:center;font-size:14px}
</style>
</head>
<body>

<!-- top bar -->
<div class="abs topbar">
  <div class="item" style="left:110px">
    <svg width="13" height="13" viewBox="0 0 24 24" fill="#fff"><path d="M6.6 10.8a15 15 0 0 0 6.6 6.6l2.2-2.2a1 1 0 0 1 1-.25 11.4 11.4 0 0 0 3.6.57 1 1 0 0 1 1 1V20a1 1 0 0 1-1 1A17 17 0 0 1 3 4a1 1 0 0 1 1-1h3.5a1 1 0 0 1 1 1c0 1.25.2 2.45.57 3.57a1 1 0 0 1-.25 1z"/></svg>
    CALL US : (555) 014-2290
  </div>
  <div class="sep" style="left:364px"></div>
  <div class="item" style="left:416px">
    <svg width="15" height="11" viewBox="0 0 24 17" fill="#fff"><path d="M1 1h22L12 10z M1 2.5l11 9 11-9V16H1z"/></svg>
    <b>EMAIL US :</b> eat@thecopperkitebrookvale.com
  </div>
  <div class="sep" style="left:751px"></div>
  <div class="item" style="left:793px">
    <svg width="13" height="13" viewBox="0 0 24 24" fill="#fff"><path d="M3 5h18v17H3zM7 2h2v5H7zM15 2h2v5h-2z"/><path d="M5 10h14v10H5z" fill="#f7941d"/><path d="M8 14l3 3 5-6" stroke="#fff" stroke-width="2" fill="none"/></svg>
    <b>AVAILABILITY:</b> SAT. - SUN.8 A.M. - 3 P.M.
  </div>
</div>

<!-- header -->
<header class="abs header">
  <div class="brand">
    <div class="name">The Copper Kite</div>
    <div class="tag">a finer diner</div>
  </div>
  <nav class="nav">
    <a class="active" style="left:0">HOME</a>
    <a style="left:87px">ABOUT US</a>
    <a style="left:203px">MENU</a>
    <a style="left:300px">RETAIL</a>
    <a style="left:400px">PRESS</a>
    <a style="left:499px">CONTACT US</a>
  </nav>
  <svg class="abs" style="left:995px;top:32px" width="26" height="26" viewBox="0 0 24 24" fill="none" stroke="#111" stroke-width="2.2"><circle cx="10" cy="10" r="7"/><path d="M15 15l7 7"/></svg>
  <svg class="abs" style="left:1046px;top:30px" width="32" height="30" viewBox="0 0 32 30" fill="none" stroke="#111" stroke-width="2.2"><path d="M1 3h5l4 17h17l3-12H8"/><circle cx="12" cy="26" r="2"/><circle cx="25" cy="26" r="2"/></svg>
  <div class="cart-count">0</div>
</header>

<!-- hero -->
<section class="abs hero">
  <div class="hero-bg"></div>
  <div class="hero-photo" role="img" aria-label="Golden waffles scattered with raspberries, blueberries and red currants on a stone surface"></div>
  <svg class="abs" style="left:0;top:505px" width="1200" height="80" viewBox="0 0 1200 80" preserveAspectRatio="none"><path fill="#fff" d="M0 60 L60 64 L140 58 L230 63 L320 56 L420 60 L520 52 L600 48 L660 42 L720 40 L800 34 L860 30 L930 24 L1000 20 L1080 14 L1150 10 L1200 6 L1200 80 L0 80Z"/></svg>
  <div class="abs display welcome">Welcome to</div>
  <h1 class="display">The Copper Kite</h1>
  <p>The doors of The Copper Kite: a finer diner were eagerly thrown open for the first time on December 28th 2004.</p>
  <div class="btn" style="left:110px;top:325px;width:171px;height:46px">Get Started</div>
</section>

<!-- about -->
<section class="about">
  <div class="abs about-frame"></div>
  <div class="abs about-photo" role="img" aria-label="Diner storefront with yellow tiled facade and illuminated sign"></div>
  <h2 class="abs display about-title">About Us</h2>
  <p class="abs about-text">The doors of The Copper Kite: a finer diner were eagerly thrown open for the first time on December 28th 2004. We welcomed our first customers and started our magnificent life as a business that continues on through today. Along with our beloved and inquisitive customers came the many questions of our origin. The most important of which we will address right here and now... "Why?" they asked "Why did you name your restaurant</p>
  <div class="btn" style="left:629px;top:1130px;width:171px;height:47px">Read More</div>
</section>

<!-- specials -->
<section class="abs specials">
  <svg width="1200" height="676" viewBox="0 0 1200 676" preserveAspectRatio="none"><path fill="#f7941d" d="M0 20 L80 26 L150 14 L230 22 L320 8 L420 18 L520 6 L600 14 L700 4 L800 12 L900 0 L1000 10 L1100 2 L1200 8 L1200 620 L1120 612 L1040 624 L960 614 L880 626 L800 618 L700 630 L620 620 L520 632 L420 622 L320 636 L220 626 L120 640 L40 630 L0 640Z"/></svg>
</section>
<h2 class="abs display specials-title">Our Daily Specials</h2>
<div class="abs side-card" style="left:0;width:163px"></div>
<div class="abs side-card" style="left:1024px;width:176px"><div class="sc-photo" style="left:6px;width:170px" role="img" aria-label="Burger on a checkered diner plate"></div></div>
<article class="abs card">
  <div class="photo" role="img" aria-label="Stacked burger with cheese and lettuce on a checkered plate"></div>
  <h3>Burger</h3>
  <p>Lorem Ipsum is simply dummy text of the printing and typesetting industry. Lorem Ipsum has been the industry's standard dummy text ever since the 1500s,</p>
  <div class="meta">
    <span><svg width="30" height="30" viewBox="0 0 30 30" fill="none" stroke="#333" stroke-width="1.5"><circle cx="15" cy="15" r="12"/><path d="M15 7v8l5 4"/></svg>220 KCAL</span>
    <span><svg width="24" height="24" viewBox="0 0 24 24" fill="none" stroke="#333" stroke-width="1.6"><path d="M4 4l16 16M20 4L4 20"/></svg>Low Fat</span>
  </div>
  <div class="btn" style="left:374px;top:243px;width:171px;height:47px">Add To Cart</div>
</article>
<div class="arrow" style="left:196px;top:1579px"><svg width="24" height="18" viewBox="0 0 24 18" fill="none" stroke="#111" stroke-width="2"><path d="M23 9H2M9 2L2 9l7 7"/></svg></div>
<div class="arrow" style="left:945px;top:1579px"><svg width="24" height="18" viewBox="0 0 24 18" fill="none" stroke="#111" stroke-width="2"><path d="M1 9h21M15 2l7 7-7 7"/></svg></div>

<!-- menu -->
<h2 class="abs display menu-title">Our Menu</h2>
<div class="dish" style="left:110px;top:2073px"><div class="thumb" style="background:linear-gradient(135deg,#4b4a2c,#8a5a2b,#c9843d)" role="img" aria-label="Roasted potatoes with sautéed greens"></div><h4>Classic Vanilla</h4><p>Lorem Ipsum is simply dummy text of the printing and typesetting industry.</p><div class="price">$8.00</div></div>
<div class="dish" style="left:604px;top:2073px"><div class="thumb" style="background:linear-gradient(135deg,#b22a2a,#3f7d2a,#d8b35a)" role="img" aria-label="Plate with peppers and grilled vegetables"></div><h4>Classic Vanilla</h4><p>Lorem Ipsum is simply dummy text of the printing and typesetting industry.</p><div class="price">$8.00</div></div>
<div class="dish" style="left:110px;top:2296px"><div class="thumb" style="background:linear-gradient(135deg,#7a2a24,#c98a3a,#5a3a22)" role="img" aria-label="Waffles with toppings at a diner counter"></div><h4>Classic Vanilla</h4><p>Lorem Ipsum is simply dummy text of the printing and typesetting industry.</p><div class="price">$8.00</div></div>
<div class="dish" style="left:604px;top:2296px"><div class="thumb" style="background:linear-gradient(135deg,#5a3b2a,#b8612e,#d98e4a)" role="img" aria-label="Roasted sweet potatoes and meat"></div><h4>Classic Vanilla</h4><p>Lorem Ipsum is simply dummy text of the printing and typesetting industry.</p><div class="price">$8.00</div></div>
<div class="dish" style="left:110px;top:2518px"><div class="thumb" style="background:linear-gradient(135deg,#6b3b1e,#a96b2f,#c9a070)" role="img" aria-label="Burger on a checkered plate"></div><h4>Classic Vanilla</h4><p>Lorem Ipsum is simply dummy text of the printing and typesetting industry.</p><div class="price">$8.00</div></div>
<div class="dish" style="left:604px;top:2518px"><div class="thumb" style="background:linear-gradient(135deg,#2a2320,#d99a3c,#f0b65a)" role="img" aria-label="Stack of golden waffles"></div><h4>Classic Vanilla</h4><p>Lorem Ipsum is simply dummy text of the printing and typesetting industry.</p><div class="price">$8.00</div></div>
<div class="dish" style="left:110px;top:2741px"><div class="thumb" style="background:linear-gradient(135deg,#333a3d,#5e9b3a,#e9ecef)" role="img" aria-label="Fresh green salad in a white bowl"></div><h4>Classic Vanilla</h4><p>Lorem Ipsum is simply dummy text of the printing and typesetting industry.</p><div class="price">$8.00</div></div>
<div class="dish" style="left:604px;top:2741px"><div class="thumb" style="background:linear-gradient(135deg,#2b2b2b,#8a6a3a,#4f7a2e)" role="img" aria-label="Grilled chicken over a grain salad"></div><h4>Classic Vanilla</h4><p>Lorem Ipsum is simply dummy text of the printing and typesetting industry.</p><div class="price">$8.00</div></div>
<div class="btn" style="left:511px;top:3011px;width:171px;height:47px">View More</div>

<!-- faq -->
<h2 class="abs display faq-title">Frequently Asked Questions</h2>
<div class="faq open" style="left:110px;top:3214px"><span>Do you take reservations?</span><span class="sign">−</span></div>
<p class="abs faq-answer">No. We are first come, first serve. This means we don't do any call-ahead seating either...</p>
<div class="faq" style="left:110px;top:3343px"><span>Do you do carry-out?</span><span class="sign">+</span></div>
<div class="faq" style="left:603px;top:3214px"><span>Do you do carry-out?</span><span class="sign">+</span></div>
<div class="faq" style="left:603px;top:3278px"><span>How large is your restaurant?</span><span class="sign">+</span></div>
<div class="faq" style="left:603px;top:3343px"><span>Why didn't you answer my question?</span><span class="sign">+</span></div>

<!-- newsletter -->
<section class="abs newsletter">
  <svg width="1200" height="360" viewBox="0 0 1200 360" preserveAspectRatio="none"><defs><linearGradient id="newsGlow" x1="0" y1="0" x2="1" y2="1"><stop offset="0" stop-color="#f7941d"/><stop offset="1" stop-color="#ef8a10"/></linearGradient></defs><path fill="url(#newsGlow)" d="M0 60 L90 52 L180 60 L270 46 L360 54 L460 40 L560 48 L660 34 L760 40 L860 26 L960 32 L1060 18 L1140 24 L1200 14 L1200 360 L0 360Z"/></svg>
</section>
<h2 class="abs display news-title">Get Update About New Dishes And<br>Upcoming Events</h2>
<p class="abs news-text">Lorem Ipsum is simply dummy text of the printing and typesetting industry. Lorem Ipsum has been the industry's standard dummy text ever since the 1500s,</p>
<div class="abs subscribe">Subscribe Now</div>

<!-- footer -->
<footer class="abs footer">
  <div class="brand">
    <div class="name">The Copper Kite</div>
    <div class="tag">a finer diner</div>
  </div>
  <div class="social" style="left:122px"></div>
  <div class="social" style="left:186px"></div>
  <div class="social active" style="left:249px"></div>

  <div class="fcol" style="left:407px">
    <h5>Main Links</h5>
    <ul><li>Home</li><li>About Us</li><li>Menu</li><li>Retail</li><li>Press</li><li>Contact Us</li></ul>
  </div>
  <div class="fcol" style="left:622px">
    <h5>Other Links</h5>
    <ul><li>Terms &amp; Conditions</li><li>Privacy Policy</li></ul>
  </div>
  <div class="fcol contact" style="left:885px">
    <h5 style="margin-left:-20px">Contact Details</h5>
    <ul>
      <li class="label"><svg width="12" height="12" viewBox="0 0 24 24" fill="#fff"><path d="M6.6 10.8a15 15 0 0 0 6.6 6.6l2.2-2.2a1 1 0 0 1 1-.25 11.4 11.4 0 0 0 3.6.57 1 1 0 0 1 1 1V20a1 1 0 0 1-1 1A17 17 0 0 1 3 4a1 1 0 0 1 1-1h3.5a1 1 0 0 1 1 1c0 1.25.2 2.45.57 3.57a1 1 0 0 1-.25 1z"/></svg>Call Us</li>
      <li class="val">(555) 014-2290</li>
      <li class="label"><svg width="13" height="10" viewBox="0 0 24 17" fill="#fff"><path d="M1 1h22L12 10z M1 2.5l11 9 11-9V16H1z"/></svg>Mail Us</li>
      <li class="val">eat@thecopperkitebrookvale.com</li>
      <li class="label"><svg width="12" height="14" viewBox="0 0 24 28" fill="#fff"><path d="M12 0a9 9 0 0 0-9 9c0 7 9 19 9 19s9-12 9-19a9 9 0 0 0-9-9zm0 13a4 4 0 1 1 0-8 4 4 0 0 1 0 8z"/></svg>Location</li>
      <li class="val">4120 Larkspur Avenue</li>
      <li class="val">Brookvale, Ohio 45012</li>
      <li class="label"><svg width="13" height="13" viewBox="0 0 24 24" fill="none" stroke="#fff" stroke-width="2"><circle cx="12" cy="12" r="10"/><path d="M12 6v6l4 3"/></svg>Working Hours</li>
      <li class="val">Sat. - Sun. 8 a.m. - 3 p.m.</li>
    </ul>
  </div>
  <div class="rule"></div>
  <div class="copy">© 2024 The Copper Kite I All Rights Reserved</div>
</footer>

</body>
</html>
```